Company Profile for Academic and Study Abroad Services

I am looking for Power Point Design for company Profile . the company is academic and study abroad services. you can visit the website which is www.korvapath.ae . the colour i prefer is Dark Blue + White + Black . you can find all the content for power point and logo and some picture i need you to add it.

Target Market(s)

Students who wants to study abroad. Universities . Learning centre.

Industry/Entity Type

Education

Font styles to use
Serif
Sans Serif

Colors
0555a3
ffffff
000000
aaaaaa

Requirements
Must have
• Must Have Images for each slides.
Nice to have
• infographic. Images related to the study abroad

```html
<!DOCTYPE html>
<html lang="en">
<head>
<meta charset="utf-8">
<title>Korva Path – Company Profile Slides</title>
<link rel="stylesheet" href="https://fonts.googleapis.com/css2?family=Source+Sans+3:wght@400;600;700&display=swap">
<style>
  :root{
    --navy:#1c2d66;
    --navy-deep:#16244f;
    --grey:#c9cbce;
    --grey-mid:#a9adb2;
    --head-band:#eceef1;
    --ink-soft:#8c939c;
    --ink-label:#9aa1a9;
    --amber:#f5b21a;
    --cover-dark:#2a2526;
    --white:#ffffff;
    --stage-a:#8b8b8b;
    --stage-b:#555555;
  }
  *{box-sizing:border-box;margin:0;padding:0}
  html,body{width:1200px;height:1200px;overflow:hidden}
  body{
    font-family:"Source Sans 3",sans-serif;
    background:radial-gradient(ellipse at 60% 30%,var(--stage-a) 0%,var(--stage-b) 100%);
    position:relative;
  }
  .slide{
    position:absolute;width:514px;height:307px;background:var(--white);
    overflow:hidden;box-shadow:0 1px 3px rgba(0,0,0,.35);
  }
  .slide--cover{left:80px;top:138px;background:var(--cover-dark)}
  .slide--who{left:628px;top:138px}
  .slide--destination{left:80px;top:478px}
  .slide--services{left:628px;top:478px}
  .slide--levels{left:80px;top:818px}
  .slide--why{left:628px;top:818px}

  .slide-head{
    position:absolute;left:0;top:0;width:100%;height:47px;
    background:var(--head-band);border-top:6px solid var(--navy);
  }
  .slide-title{
    position:absolute;top:11px;font-size:15px;font-weight:700;
    color:var(--navy);letter-spacing:.1px;
  }
  .brand{
    position:absolute;display:flex;align-items:center;gap:3px;
    font-weight:700;color:var(--navy);white-space:nowrap;
  }
  .brand-mark{display:block;background:var(--navy)}
  .slide-head .brand{right:12px;top:13px;font-size:7px}
  .slide-head .brand-mark{width:7px;height:7px}

  .body-copy{position:absolute;color:var(--ink-soft);font-size:5.6px;line-height:1.38}
  .body-copy p{margin-bottom:4px}
  .copy-heading{font-weight:700;font-size:5.6px;color:var(--ink-label);margin-bottom:7px;letter-spacing:.2px}

  .art{position:absolute;left:0;top:0;width:514px;height:307px}

  /* cover */
  .cover-photo{
    position:absolute;left:0;top:0;width:514px;height:307px;
    clip-path:polygon(0 0,338px 0,343px 307px,0 307px);
    background:linear-gradient(160deg,#4a3b33 0%,#7a5e4c 35%,#3d3434 65%,#5c5f4a 100%);
  }
  .cover-title{position:absolute;left:60px;top:228px;color:var(--white);line-height:1.25}
  .cover-title .name{font-size:15px;font-weight:700;display:block}
  .cover-title .tagline{font-size:14px;font-weight:600;display:block}
  .slide--cover .brand{right:14px;bottom:16px;font-size:11px}
  .slide--cover .brand-mark{width:10px;height:10px}

  /* who we are */
  .map-panel{position:absolute;left:257px;top:47px;width:257px;height:134px;
    background:linear-gradient(180deg,#c3c5c8,#b9bcbf)}
  .navy-panel{position:absolute;left:257px;top:181px;width:257px;height:126px;background:var(--navy)}
  .portrait{position:absolute;left:244px;top:132px;width:99px;height:127px;
    background:linear-gradient(160deg,#5a5a5a,#1e1e1e 70%,#2e2e2e)}
  .panel-copy{position:absolute;left:370px;top:200px;width:128px;color:var(--white);
    font-size:5.6px;font-weight:700;line-height:1.35}
  .panel-copy p{margin-bottom:5px}

  /* percentages */
  .stat{position:absolute;width:60px;margin-left:-30px;text-align:center;font-size:15px;color:var(--white)}
  .ring-value{position:absolute;width:60px;margin-left:-30px;text-align:center;font-size:15px;color:var(--ink-label)}
  .ring-label{position:absolute;width:80px;margin-left:-40px;text-align:center;font-size:7px;font-weight:600;color:var(--ink-label)}

  /* services */
  .option{position:absolute;width:80px;margin-left:-40px;text-align:center;
    color:var(--ink-soft);font-size:5.6px;line-height:1.35}
  .option b{display:block;font-weight:400;font-size:5.8px;color:var(--ink-label)}
  .gear-num{font-family:"Source Sans 3",sans-serif}

  /* levels */
  .level-list{position:absolute;left:120px;top:198px;width:320px;list-style:none;
    color:var(--ink-soft);font-size:5.6px;line-height:1.4}
  .level-list li{position:relative;padding-left:16px;margin-bottom:6px}
  .level-list li::before{content:"";position:absolute;left:3px;top:2px;width:5px;height:5px;border-radius:50%;background:var(--navy)}
  .level-list li.is-grey::before{background:var(--grey)}
</style>
</head>
<body>

<!-- Cover -->
<section class="slide slide--cover">
  <div class="cover-photo" role="img" aria-label="Group photo of smiling students sitting together on a staircase"></div>
  <svg class="art" viewBox="0 0 514 307" aria-hidden="true">
    <polygon points="382,0 390,0 514,212 514,226" fill="#d9dbde"/>
    <polygon points="341,307 400,78 514,270 514,307" fill="#d2d4d7"/>
    <polygon points="334,307 396,70 403,70 342,307" fill="var(--navy)"/>
    <polygon points="345,0 372,0 514,243 514,290" fill="var(--navy)"/>
    <polygon points="470,307 514,260 514,307" fill="var(--navy-deep)" opacity=".0"/>
  </svg>
  <div class="cover-title">
    <span class="name">KORVA PATH</span>
    <span class="tagline">Universities Entrance Services</span>
  </div>
  <div class="brand"><span class="brand-mark"></span>KORVA PATH</div>
</section>

<!-- Who we are -->
<section class="slide slide--who">
  <header class="slide-head"><h2 class="slide-title" style="left:26px">WHO WE ARE</h2>
    <div class="brand"><span class="brand-mark"></span>KORVA PATH</div></header>
  <div class="body-copy" style="left:35px;top:92px;width:208px">
    <div class="copy-heading">LOREM IPSUM DOLOR</div>
    <p>We guide students from first enquiry to final enrolment, matching each learner with universities that fit their goals, grades and budget across the world.</p>
    <p>Our advisers review transcripts, prepare applications and track every deadline so families always know the next step. We also support visa paperwork and housing.</p>
    <p>Partner schools trust us to send prepared, motivated applicants, and learning centres use our workshops to build study skills before departure.</p>
  </div>
  <div class="map-panel" role="img" aria-label="Flat world map in white on grey"></div>
  <div class="navy-panel"></div>
  <div class="portrait" role="img" aria-label="Black and white portrait photograph of an inspirational leader"></div>
  <div class="panel-copy">
    <p>Every student deserves a clear path. Our advisers listen first and plan second.</p>
    <p>Honest advice, careful planning and steady follow-up at each stage.</p>
    <p>One team from offer to arrival</p>
  </div>
</section>

<!-- Study destination -->
<section class="slide slide--destination">
  <header class="slide-head"><h2 class="slide-title" style="left:37px">STUDY DESTINATION</h2>
    <div class="brand"><span class="brand-mark"></span>KORVA PATH</div></header>
  <div class="body-copy" style="left:36px;top:88px;width:200px">
    <div class="copy-heading">LOREM IPSUM DOLOR</div>
    <p>Choose from leading universities in the UK, Canada, Australia, Europe and Asia. We compare fees, rankings and entry rules for each course.</p>
    <p>Most of our students secure an offer from their first or second choice within one intake cycle.</p>
    <p>Scholarship searches and budget plans are included with every application package.</p>
  </div>
  <svg class="art" viewBox="0 0 514 307" aria-hidden="true">
    <circle cx="384" cy="148" r="92" fill="var(--grey)"/>
    <circle cx="384" cy="175" r="74" fill="var(--navy)"/>
    <rect x="180" y="264" width="81" height="6" fill="var(--grey)"/>
    <rect x="261" y="262" width="90" height="8" fill="var(--navy)"/>
    <rect x="351" y="259" width="119" height="11" fill="var(--navy)"/>
  </svg>
  <div class="stat" style="left:384px;top:74px">100%</div>
  <div class="stat" style="left:384px;top:109px">85%</div>
  <div class="stat" style="left:384px;top:143px">60%</div>
</section>

<!-- What we do -->
<section class="slide slide--services">
  <header class="slide-head"><h2 class="slide-title" style="left:45px">WHAT WE DO</h2>
    <div class="brand"><span class="brand-mark"></span>KORVA PATH</div></header>
  <div class="body-copy" style="left:35px;top:78px;width:222px">
    <p>Personal counselling sessions help students shape a shortlist of courses and universities that suit their strengths.</p>
    <p>We prepare documents, personal statements and references, then submit on time.</p>
    <p>After an offer arrives we handle visas, travel and arrival support for a smooth start.</p>
  </div>
  <svg class="art" viewBox="0 0 514 307" aria-hidden="true">
    <g fill="none" stroke="var(--grey-mid)" stroke-width=".8">
      <polyline points="333,113 349,99 406,99"/>
      <polyline points="367,197 381,177 430,177"/>
      <polyline points="185,259 230,259 243,240"/>
    </g>
    <!-- gear 03 -->
    <g transform="translate(338 234)">
      <circle r="42" fill="none" stroke="var(--grey)" stroke-width="9" stroke-dasharray="9.42 9.42"/>
      <circle r="38" fill="var(--grey)"/>
      <circle r="26" fill="var(--white)"/>
      <text class="gear-num" y="9" text-anchor="middle" font-size="26" fill="var(--grey-mid)">03</text>
    </g>
    <!-- gear 02 -->
    <g transform="translate(309 150)">
      <circle r="37" fill="none" stroke="var(--navy)" stroke-width="8" stroke-dasharray="9.7 9.7"/>
      <circle r="34" fill="var(--navy)"/>
      <circle r="24" fill="var(--white)"/>
      <text class="gear-num" y="8" text-anchor="middle" font-size="23" fill="var(--grey-mid)">02</text>
    </g>
    <!-- gear 01 -->
    <g transform="translate(258 208)">
      <circle r="26" fill="none" stroke="var(--navy)" stroke-width="6" stroke-dasharray="8.17 8.17"/>
      <circle r="23" fill="var(--navy)"/>
      <circle r="15" fill="var(--white)"/>
      <text class="gear-num" y="6" text-anchor="middle" font-size="16" fill="var(--navy)">01</text>
    </g>
    <!-- target icon -->
    <g transform="translate(417 99)" fill="none" stroke="var(--grey-mid)">
      <circle r="8" stroke-width="2"/><circle r="4" stroke-width="1.6"/>
      <circle r="1.3" fill="var(--grey-mid)" stroke="none"/>
      <line x1="2" y1="-2" x2="9" y2="-9" stroke-width="1.4"/>
    </g>
    <!-- clock icon -->
    <g transform="translate(440 177)" fill="none" stroke="var(--grey-mid)" stroke-width="1.6">
      <circle r="7.5"/><polyline points="0,-4 0,0 3,2"/>
      <line x1="-7" y1="-8" x2="-4" y2="-10"/><line x1="7" y1="-8" x2="4" y2="-10"/>
    </g>
    <!-- coin icon -->
    <g transform="translate(172 259)">
      <circle r="9.5" fill="var(--grey-mid)"/>
      <text y="4" text-anchor="middle" font-size="12" font-weight="700" fill="var(--white)" font-family="Source Sans 3, sans-serif">$</text>
    </g>
  </svg>
  <div class="option" style="left:421px;top:113px"><b>2 OPTION</b>Application review and submission for every course.</div>
  <div class="option" style="left:442px;top:193px"><b>3 OPTION</b>Visa filing, travel and arrival planning.</div>
  <div class="option" style="left:173px;top:205px"><b>1 OPTION</b>Free first meeting and course advice.</div>
</section>

<!-- Education levels -->
<section class="slide slide--levels">
  <header class="slide-head"><h2 class="slide-title" style="left:44px">EDUCATION LEVELS</h2>
    <div class="brand"><span class="brand-mark"></span>KORVA PATH</div></header>
  <svg class="art" viewBox="0 0 514 307" aria-hidden="true">
    <g fill="none">
      <g transform="translate(108 128)">
        <circle r="61" pathLength="100" stroke="var(--navy)" stroke-width="6" stroke-dasharray="55 45" transform="rotate(150)"/>
        <circle r="61" pathLength="100" stroke="var(--grey)" stroke-width="6" stroke-dasharray="26 74" transform="rotate(358)"/>
        <circle r="49" pathLength="100" stroke="var(--navy)" stroke-width="7" stroke-dasharray="72 28" transform="rotate(40)"/>
        <circle r="36" pathLength="100" stroke="var(--navy)" stroke-width="7" stroke-dasharray="70 30" transform="rotate(55)"/>
        <circle r="24" pathLength="100" stroke="var(--navy)" stroke-width="6" stroke-dasharray="66 34" transform="rotate(48)"/>
      </g>
      <g transform="translate(257 128)">
        <circle r="57" pathLength="100" stroke="var(--navy)" stroke-width="7" stroke-dasharray="78 22" transform="rotate(10)"/>
        <circle r="45" pathLength="100" stroke="var(--navy)" stroke-width="7" stroke-dasharray="60 40" transform="rotate(110)"/>
        <circle r="45" pathLength="100" stroke="var(--grey)" stroke-width="7" stroke-dasharray="30 70" transform="rotate(340)"/>
        <circle r="33" pathLength="100" stroke="var(--navy)" stroke-width="7" stroke-dasharray="70 30" transform="rotate(60)"/>
        <circle r="21" pathLength="100" stroke="var(--grey)" stroke-width="6" stroke-dasharray="60 40" transform="rotate(80)"/>
      </g>
      <g transform="translate(407 128)">
        <circle r="57" pathLength="100" stroke="var(--grey)" stroke-width="5" stroke-dasharray="28 72" transform="rotate(260)"/>
        <circle r="50" pathLength="100" stroke="var(--navy)" stroke-width="7" stroke-dasharray="80 20" transform="rotate(-10)"/>
        <circle r="38" pathLength="100" stroke="var(--navy)" stroke-width="7" stroke-dasharray="45 55" transform="rotate(120)"/>
        <circle r="38" pathLength="100" stroke="var(--grey)" stroke-width="7" stroke-dasharray="22 78" transform="rotate(40)"/>
        <circle r="26" pathLength="100" stroke="var(--navy)" stroke-width="6" stroke-dasharray="72 28" transform="rotate(-40)"/>
      </g>
    </g>
  </svg>
  <ul class="level-list">
    <li>FOUNDATION PROGRAMMES prepare school leavers for university entry with language and core subject study.</li>
    <li class="is-grey">UNDERGRADUATE DEGREES cover bachelor courses in business, engineering, medicine, arts and the sciences.</li>
    <li>POSTGRADUATE STUDY includes master and doctoral programmes with research and taught options.</li>
  </ul>
</section>

<!-- Why choose -->
<section class="slide slide--why">
  <header class="slide-head"><h2 class="slide-title" style="left:29px">WHY CHOOSE KORVA PATH</h2>
    <div class="brand"><span class="brand-mark"></span>KORVA PATH</div></header>
  <svg class="art" viewBox="0 0 514 307" aria-hidden="true">
    <g fill="none" stroke-width="8">
      <g transform="translate(112 126)">
        <polygon points="-6,38 6,38 0,46" fill="var(--amber)" stroke="none"/>
        <circle r="38" pathLength="100" stroke="var(--amber)" stroke-dasharray="50 50" transform="rotate(-80)"/>
        <circle r="38" pathLength="100" stroke="var(--grey)" stroke-dasharray="15 85" transform="rotate(100)"/>
        <circle r="38" pathLength="100" stroke="var(--navy)" stroke-dasharray="35 65" transform="rotate(154)"/>
      </g>
      <g transform="translate(208 126)">
        <polygon points="-6,38 6,38 0,46" fill="var(--grey)" stroke="none"/>
        <circle r="38" pathLength="100" stroke="var(--navy)" stroke-dasharray="68 32" transform="rotate(-98)"/>
        <circle r="38" pathLength="100" stroke="var(--grey)" stroke-dasharray="12 88" transform="rotate(147)"/>
        <circle r="38" pathLength="100" stroke="var(--amber)" stroke-dasharray="20 80" transform="rotate(190)"/>
      </g>
      <g transform="translate(304 126)">
        <polygon points="-6,38 6,38 0,46" fill="var(--navy)" stroke="none"/>
        <circle r="38" pathLength="100" stroke="var(--grey)" stroke-dasharray="40 60" transform="rotate(-120)"/>
        <circle r="38" pathLength="100" stroke="var(--navy)" stroke-dasharray="30 70" transform="rotate(24)"/>
        <circle r="38" pathLength="100" stroke="var(--amber)" stroke-dasharray="30 70" transform="rotate(132)"/>
      </g>
      <g transform="translate(400 126)">
        <polygon points="-6,38 6,38 0,46" fill="var(--navy)" stroke="none"/>
        <circle r="38" pathLength="100" stroke="var(--navy)" stroke-dasharray="70 30" transform="rotate(-120)"/>
        <circle r="38" pathLength="100" stroke="var(--grey)" stroke-dasharray="30 70" transform="rotate(132)"/>
      </g>
    </g>
  </svg>
  <div class="ring-value" style="left:112px;top:115px">50%</div>
  <div class="ring-value" style="left:208px;top:115px">70%</div>
  <div class="ring-value" style="left:304px;top:115px">55%</div>
  <div class="ring-value" style="left:400px;top:115px">40%</div>
  <div class="ring-label" style="left:112px;top:185px">LOREM IPSUM</div>
  <div class="ring-label" style="left:208px;top:185px">LOREM IPSUM</div>
  <div class="ring-label" style="left:304px;top:185px">LOREM IPSUM</div>
  <div class="ring-label" style="left:400px;top:185px">LOREM IPSUM</div>
  <div class="body-copy" style="left:35px;top:228px;width:390px">
    <p>Our advisers have placed students at hundreds of universities and know each admissions team well. We keep fees clear and agree every step in writing.</p>
    <p>Families receive regular updates, and students keep a named adviser until they settle abroad.</p>
  </div>
</section>

</body>
</html>
```